Allied Health team of Physiotherapists & Occupational Therapists seek a business card design

We have our new logo, we now need our new business cards and stationary. Tidewell: Oedema & Family Clinic is seeking a generic card design to represent our whole team and individual cards for each therapist that incorporates our new logo to communicate our holistic approach that is calming, nuturing, supportive and welcoming.
Our Physiotherapists and Occupational Therapists assess, treat and provide education for people who are at risk of or who have lymphoedema. This is often as a result of treatment for cancer. We provide pre-operative and post-operative management and cancer rehabilitation in our Pilates studio. Our team also consists of Physiotherapists who have a strong interest in pelvic floor and continence management for both men and women.

Target Market(s)

Mainly women health conscious

Industry/Entity Type

Allied Health: Physiotherapy / Occupational Therapy

Contact Information for Business Card

Address: 14 Gallivant Ave Seabrook 3218 Phone: 84316570 fax: 8431 6578 Email: info@tidewellcareservices.com.au Website: tidewellcareservices.com.au Facebook address: facebook.com/TidewellOedemaAndFamilyCareClinic. Room to write appointments. Individual cards need to have name, office email and individual email and professional details

Requirements
Must have
• Logo as per uploaded documents

```html
<!DOCTYPE html>
<html lang="en">
<head>
<meta charset="utf-8">
<title>Tidewell Business Cards</title>
<link href="https://fonts.googleapis.com/css2?family=Alice&family=Lato:ital,wght@0,300;0,400;1,400&display=swap" rel="stylesheet">
<style>
  :root{
    --bg:#9b9b9b;
    --card-white:#ffffff;
    --card-cream:#fef9d9;
    --peach:#f6a877;
    --peach-faint:#fcebdf;
    --sage:#c3cbbd;
    --ink:#4a4a4a;
    --ink-soft:#5e5e5e;
  }
  *{box-sizing:border-box;margin:0;padding:0}
  html,body{width:1133px;height:1200px;overflow:hidden;background:var(--bg)}
  body{position:relative;font-family:'Lato',sans-serif;color:var(--ink)}
  .card{position:absolute;left:219px;width:693px;height:397px;overflow:hidden}
  .card--front{top:152px;background:var(--card-white)}
  .card--back{top:648px;background:var(--card-cream)}

  /* appointment side */
  .watermark{position:absolute;left:213px;top:45px;width:270px;height:270px;border-radius:50%;
    border:2px solid var(--peach-faint)}
  .watermark-name{position:absolute;left:0;top:62px;width:100%;text-align:center;
    font-family:'Alice',serif;font-size:24px;color:var(--peach-faint)}
  .appt-title{position:absolute;top:120px;left:0;width:100%;text-align:center;
    font-family:'Alice',serif;font-weight:400;font-size:29px;color:var(--peach)}
  .field{position:absolute;left:135px;font-size:16px;color:var(--ink);display:flex;align-items:flex-end;gap:4px}
  .field .rule{border-bottom:1px solid var(--ink);height:14px}
  .field--name{top:203px;width:423px}
  .field--name .rule{flex:1}
  .field--date{top:239px;width:423px}
  .field--date .rule.date{width:219px}
  .field--date .rule.time{flex:1}
  .book{position:absolute;top:323px;left:181px;font-size:16px;color:var(--ink);display:flex;align-items:center;gap:7px}
  .book .pill{background:var(--peach);color:#fff;border-radius:10px;padding:1px 8px 2px}

  /* contact side */
  .bar{position:absolute;left:0;width:6px;border-radius:0 3px 3px 0}
  .bar--peach{top:55px;height:133px;background:var(--peach)}
  .bar--sage{top:212px;height:134px;background:var(--sage)}
  .person-name{position:absolute;left:30px;top:50px;font-family:'Alice',serif;font-weight:400;font-size:25px;color:var(--peach)}
  .credentials{position:absolute;left:29px;top:82px;font-size:12.6px;font-style:italic;font-weight:400;line-height:17.3px;color:var(--ink-soft)}
  .roles{position:absolute;left:29px;top:134px;font-size:16.5px;line-height:18.5px;color:var(--ink)}
  .contacts{position:absolute;left:29px;top:208px;list-style:none;font-size:16.5px;line-height:20px;color:var(--ink)}
  .contacts li{display:flex;align-items:center;gap:8px}
  .contacts svg{width:14px;height:14px;flex:none}
  .brand{position:absolute;left:408px;top:93px;width:240px;height:240px;border-radius:50%;
    border:2px solid var(--peach);display:flex;align-items:center;justify-content:center;text-align:center}
  .brand span{font-family:'Alice',serif;font-size:24px;line-height:30px;color:var(--peach)}
</style>
</head>
<body>

<section class="card card--front">
  <div class="watermark"><span class="watermark-name">Tidewell</span></div>
  <h1 class="appt-title">Next Appointment</h1>
  <div class="field field--name">Name: <span class="rule"></span></div>
  <div class="field field--date">Date: <span class="rule date"></span> Time: <span class="rule time"></span></div>
  <p class="book">Book Online <span class="pill">tidewellcareservices.com.au</span></p>
</section>

<section class="card card--back">
  <div class="bar bar--peach"></div>
  <div class="bar bar--sage"></div>
  <h2 class="person-name">Maren Holt</h2>
  <p class="credentials">B. Physio (Hons), B.Sc.(Exercise Science/Health Studies)<br>Grad Cert. Women's Exercise Therapy<br>Grad Cert. Pelvic Health &amp; Bladder Care Practice</p>
  <p class="roles">Physiotherapist<br>Lymphoedema &amp; Oncology Rehabilitation<br>Continence &amp; Pelvic Floor</p>
  <ul class="contacts">
    <li><svg viewBox="0 0 14 14"><path d="M7 1a4.5 4.5 0 0 0-4.5 4.5C2.5 9 7 13.5 7 13.5S11.5 9 11.5 5.5A4.5 4.5 0 0 0 7 1z" fill="#f6a877"/><circle cx="7" cy="5.5" r="1.7" fill="#fef9d9"/></svg>14 Gallivant Ave, Seabrook 3218</li>
    <li><svg viewBox="0 0 14 14"><path d="M3 1.5l2.2 2.6-1.2 1.5a8 8 0 0 0 4.4 4.4l1.5-1.2 2.6 2.2-1.4 1.8C6 12.5 1.5 8 1.2 2.9z" fill="#f6a877"/></svg>84316570 Phone</li>
    <li><svg viewBox="0 0 14 14"><rect x="4" y="1.5" width="6" height="3.5" fill="#f6a877"/><rect x="1.5" y="5" width="11" height="5" rx="1" fill="#f6a877"/><rect x="4" y="8.5" width="6" height="4" fill="#f6a877" stroke="#fef9d9"/></svg>8431 6578 Fax</li>
    <li><svg viewBox="0 0 14 14"><rect x="1.5" y="3" width="11" height="8" fill="#f6a877"/><path d="M1.8 3.4L7 7.5l5.2-4.1" stroke="#fef9d9" fill="none"/></svg>maren@tidewellcareservices.com.au</li>
    <li><svg viewBox="0 0 14 14"><rect x="1.5" y="3" width="11" height="8" fill="#f6a877"/><path d="M1.8 3.4L7 7.5l5.2-4.1" stroke="#fef9d9" fill="none"/></svg>info@tidewellcareservices.com.au (office)</li>
    <li><svg viewBox="0 0 14 14"><circle cx="7" cy="7" r="5.5" fill="#f6a877"/><path d="M1.5 7h11M7 1.5c-2.5 3-2.5 8 0 11M7 1.5c2.5 3 2.5 8 0 11" stroke="#fef9d9" fill="none" stroke-width=".8"/></svg>tidewellcareservices.com.au</li>
    <li><svg viewBox="0 0 14 14"><circle cx="7" cy="7" r="5.5" fill="#f6a877"/></svg>/TidewellOedemaAndFamilyCareClinic</li>
  </ul>
  <div class="brand"><span>Tidewell: Oedema<br>&amp; Family Clinic</span></div>
</section>

</body>
</html>
```